New Website for novelty yarn producer

We need a new website for our company, Vedrana. We make highly tailored yarns for weavers worldwide. This year marks our 40th anniversary and we want to evolve our image and identity.

Our temporary website can be found at:
www.vedranathreads.example

Our only concern in that throughout the website the protagonist must be our client, we make their creations possible and are highly adaptable both during the ideation process of the yarn as well as in the production. This is at the core of the way we do business and is summarised within the concept of FMC (Full Motion Craft).

Industry/Entity Type

Textile

Number of Pages Required

1 page

Colors
9bcb3c

Requirements
Must have
• Full Motion Craft (FMC) - can be found on or current website www.vedranathreads.example

```html
<!DOCTYPE html>
<html lang="en">
<head>
<meta charset="utf-8">
<title>Vedrana — Novelty Yarn Solutions</title>
<link href="https://fonts.googleapis.com/css2?family=Lora:wght@400;700&display=swap" rel="stylesheet">
<style>
:root{
  --green:#9bcb3c;
  --ink:#1e1e1e;
  --muted:#6b6b6b;
  --linen:#ededed;
  --white:#ffffff;
  --dark:#1f1d1b;
  --dash:#b9b9b9;
}
*{box-sizing:border-box;margin:0;padding:0}
html,body{width:1200px;height:2219px;overflow:hidden;background:var(--white)}
body{font-family:"Lora",Georgia,serif;color:var(--ink);position:relative}
.section{position:absolute;left:0;width:1200px}
.center{text-align:center}
.btn{position:absolute;left:516px;width:168px;height:40px;background:var(--green);color:var(--white);font-size:11px;font-weight:700;letter-spacing:.5px;line-height:40px;text-align:center;text-transform:uppercase}
.dashed{position:absolute;left:0;width:1200px;border-top:1px dashed var(--dash)}

/* hero */
.hero{top:0;height:522px;overflow:hidden}
.hero-photo{position:absolute;inset:0;background:linear-gradient(120deg,#2a211b 0%,#4a3a2e 35%,#35302c 60%,#5a5650 100%)}
.hero-shade{position:absolute;inset:0;background:rgba(0,0,0,.25)}
.brand{position:absolute;left:74px;top:22px;display:flex;align-items:center;gap:8px;color:var(--white);font-size:34px;letter-spacing:1px}
.brand .dot{width:10px;height:10px;border-radius:50%;background:var(--green)}
.nav{position:absolute;right:50px;top:38px;display:flex;gap:30px;font-size:12px;color:var(--white);text-transform:uppercase}
.nav .active{position:relative}
.nav .active::before{content:"";position:absolute;left:-8px;right:-8px;top:-38px;height:4px;background:var(--green)}
.hero .rule{border-top-color:rgba(255,255,255,.55);top:94px}
.badge{position:absolute;left:533px;top:188px;width:134px;height:134px;border-radius:50%;border:2px solid rgba(255,255,255,.85);color:var(--white);text-align:center}
.badge b{display:block;font-weight:400;font-size:54px;line-height:1;margin-top:22px}
.badge span{font-size:15px}
.hero-title{position:absolute;left:330px;width:540px;top:330px;height:52px;border-top:1px dashed rgba(255,255,255,.6);border-bottom:1px dashed rgba(255,255,255,.6);color:var(--white);font-size:33px;line-height:50px;text-align:center;text-transform:uppercase}
.hero .btn{top:397px}

/* values */
.values{top:522px;height:304px;background:var(--linen)}
.value{position:absolute;top:32px;width:300px;text-align:center}
.value .icon{width:90px;height:90px;margin:0 auto;border-radius:50%}
.value .icon.accent{background:var(--green)}
.value .icon.plain{background:#2b2b2b}
.value h3{width:220px;margin:23px auto 0;border-top:1px solid var(--green);border-bottom:1px solid var(--green);font-weight:400;font-size:22px;line-height:46px;text-transform:uppercase}
.value p{margin-top:12px;font-size:13px;line-height:18px;color:var(--muted)}

/* approach */
.approach{top:826px;height:367px}
.concept{position:absolute;left:458px;top:72px;display:flex;align-items:center;gap:16px}
.concept .dot{width:60px;height:60px;border-radius:50%;border:3px solid var(--green)}
.concept .bar{width:2px;height:88px;background:var(--ink)}
.concept .name{font-size:20px;line-height:22px;text-transform:uppercase}
.approach h2{position:absolute;top:190px;width:100%;font-weight:400;font-size:28px;text-transform:uppercase}
.approach p{position:absolute;top:229px;left:350px;width:500px;font-size:13px;line-height:19px;color:var(--muted)}
.approach .btn{top:286px}

/* team */
.team{top:1193px;height:305px;background:var(--linen)}
.team .lead{position:absolute;top:80px;left:190px;width:820px;font-size:20px;line-height:28px}
.team .focus{position:absolute;top:182px;width:100%;font-size:12px;font-weight:700}
.team .btn{top:218px}

/* numbers */
.numbers{top:1498px;height:478px;overflow:hidden}
.numbers-photo{position:absolute;inset:0;background:linear-gradient(100deg,#141312 0%,#2c2925 40%,#3a3732 60%,#151413 100%)}
.numbers h2{position:absolute;left:488px;width:224px;top:78px;border-top:1px solid rgba(255,255,255,.6);border-bottom:1px solid rgba(255,255,255,.6);color:var(--white);font-weight:400;font-size:26px;line-height:46px;text-transform:uppercase}
.stat{position:absolute;top:160px;width:182px;height:182px;border-radius:50%;border:2px solid rgba(255,255,255,.7);color:var(--white);text-align:center}
.stat b{display:block;font-weight:400;font-size:90px;line-height:1;color:var(--green);margin-top:28px}
.stat span{display:block;font-size:16px;line-height:17px}
.numbers .btn{top:370px}

/* footer */
.footer{top:1976px;height:243px;background:var(--linen);font-size:12px;line-height:18px;text-transform:uppercase}
.footer .brand{color:var(--ink);left:50px;top:52px}
.footer-nav{position:absolute;left:294px;top:50px;list-style:none}
.contact{position:absolute;left:514px;top:50px}
.contact .row{display:flex;gap:14px;margin-bottom:18px}
.contact svg{flex:none;margin-top:2px}
.legal{position:absolute;left:827px;top:50px}
.footer .rule{top:197px}
.copy{position:absolute;top:212px;width:100%;text-align:center}
</style>
</head>
<body>

<section class="section hero">
  <div class="hero-photo" role="img" aria-label="Photograph of a tailor measuring a client's wrist with a yellow tape measure"></div>
  <div class="hero-shade"></div>
  <div class="brand">Vedrana</div>
  <nav class="nav">
    <span class="active">Home</span><span>About us</span><span>Full Motion Craft</span><span>Heritage</span><span>Team</span><span>Blog</span><span>Contact</span>
  </nav>
  <div class="dashed rule"></div>
  <div class="badge"><b>40</b><span>Vedrana</span></div>
  <h1 class="hero-title">Tailored weaving solutions</h1>
  <a class="btn">Learn more</a>
</section>

<section class="section values">
  <div class="value" style="left:75px">
    <div class="icon accent" role="img" aria-label="Sewing machine emblem within a laurel wreath"></div>
    <h3>Experience</h3>
    <p>Over the years the company has gained the knowledge and skills that define the superiority of our product and the rigor of our work ethic</p>
  </div>
  <div class="value" style="left:450px">
    <div class="icon plain" role="img" aria-label="Needle and thread emblem within a laurel wreath"></div>
    <h3>Creativity</h3>
    <p>Over the years the company has gained the knowledge and skills that define the superiority of our product and the rigor of our work ethic</p>
  </div>
  <div class="value" style="left:810px">
    <div class="icon plain" role="img" aria-label="Dress emblem within a laurel wreath"></div>
    <h3>Professionality</h3>
    <p>Over the years the company has gained the knowledge and skills that define the superiority of our product and the rigor of our work ethic</p>
  </div>
</section>
<div class="dashed" style="top:826px"></div>

<section class="section approach center">
  <div class="concept">
    <div class="dot"></div>
    <div class="bar"></div>
    <div class="name" style="text-align:left">Full<br>Motion<br>Craft</div>
  </div>
  <h2>Production built around you</h2>
  <p>Versatility and flexibility both in development and production are key in delivering a custom solution capable of giving life to your products.</p>
  <a class="btn">Find out more</a>
</section>
<div class="dashed" style="top:1193px"></div>

<section class="section team center">
  <p class="lead">Our team has decades of experience in providing yarn solutions to weavers around the world, assisting them in the creation of outstanding textiles.Our clients can expect open lines of communication, clarity and professionality</p>
  <p class="focus">Our focus is our client.The success of a client is our success.</p>
  <a class="btn">Our heritage</a>
</section>
<div class="dashed" style="top:1497px"></div>

<section class="section numbers center">
  <div class="numbers-photo" role="img" aria-label="Dark photograph of a man in a tailored tweed jacket and bow tie"></div>
  <h2>VYS in numbers</h2>
  <div class="stat" style="left:229px"><b>40</b><span>Years In Business</span></div>
  <div class="stat" style="left:509px"><b>2</b><span>Million<br>Kilograms/Yr</span></div>
  <div class="stat" style="left:789px"><b>8</b><span>Brands</span></div>
  <a class="btn">Our heritage</a>
</section>

<footer class="section footer">
  <div class="brand">Vedrana</div>
  <ul class="footer-nav">
    <li>Home</li><li>About us</li><li>Full Motion Craft</li><li>Heritage</li><li>Team</li><li>Blog</li><li>Contact</li>
  </ul>
  <div class="contact">
    <div class="row">
      <svg width="12" height="16" viewBox="0 0 12 16"><path d="M6 0a6 6 0 0 0-6 6c0 4.5 6 10 6 10s6-5.5 6-10a6 6 0 0 0-6-6zm0 8.5A2.5 2.5 0 1 1 6 3.5a2.5 2.5 0 0 1 0 5z" fill="var(--green)"/></svg>
      <div>Vedrana Novelty Yarn Solutions<br>Corvane S.r.l Via dei Telai<br>14 - 50100 Firenze - Italy</div>
    </div>
    <div class="row">
      <svg width="14" height="14" viewBox="0 0 14 14"><path d="M3 0l2.5 3.2-1.4 1.6c.8 1.8 2.3 3.3 4.1 4.1l1.6-1.4L13 10v2.2c0 1-.8 1.8-1.8 1.8C5 14 0 9 0 2.8 0 1.8.8 1 1.8 1z" fill="var(--green)"/></svg>
      <div>Tel. 0555 018 274 R.A &nbsp;| &nbsp;Fax 0555 018 299</div>
    </div>
  </div>
  <div class="legal">R.E.A FI 481203 - Reg. Imp. FI 07184420915<br>P. IVA 07184420915 - Cod. Fisc. 07184420915<br>Capitale Sociale € 85.000,00 int. ver.</div>
  <div class="dashed rule"></div>
  <p class="copy">© 2018 Company Name | All rihgts reserved</p>
</footer>

</body>
</html>
```